New web page, 2 companies on the one page

A new web page for an engineering consultancy and maintenance management company

Corlett & Associates is the parent company covering the design and consultancy
Valtrix Engineering is the Maintenance and Reliability company

Target Market(s)

Food & Beverage, ingredients Manufacturing
engineering managers

Coding

Coded - Design and coding required

Number of Pages Required

1 page

Font styles to use
Other font styles liked:
• Roboto

Colors
1861ab
85acd3
d0dfed
cee9f5

```html
<!DOCTYPE html>
<html lang="en">
<head>
<meta charset="utf-8">
<title>Corlett &amp; Associates</title>
<link rel="stylesheet" href="https://fonts.googleapis.com/css2?family=Montserrat:wght@600;700&family=Roboto:wght@400;500;700&display=swap">
<style>
:root{
  --blue:#16a3e0;
  --blue-dark:#1861ab;
  --blue-soft:#85acd3;
  --blue-pale:#cee9f5;
  --ink:#1b1b1b;
  --text:#6d6d6d;
  --grey-bg:#f1f1f1;
  --white:#ffffff;
  --black:#000000;
}
*{box-sizing:border-box;margin:0;padding:0}
html,body{width:1200px;height:4025px;overflow:hidden;background:var(--white)}
body{position:relative;font-family:"Roboto",Arial,sans-serif;color:var(--ink)}
.abs{position:absolute}
.heading{font-family:"Montserrat",Arial,sans-serif;font-weight:700;color:var(--ink);text-transform:uppercase}
.btn{position:absolute;display:flex;align-items:center;justify-content:center;background:var(--blue);color:var(--white);font-weight:700;font-size:15px;text-transform:uppercase}

/* header */
.brand{position:absolute;left:109px;top:24px;display:flex;align-items:center;gap:12px}
.brand-mark{width:58px;height:58px;background:var(--blue-dark)}
.brand-name{font-family:"Montserrat",Arial,sans-serif;font-weight:700;font-size:26px;color:#3a3a3a;line-height:1.05}
.call{position:absolute;left:636px;top:18px;display:flex;gap:14px;align-items:center}
.call-text small{display:block;font-size:13px;color:var(--ink)}
.call-text span{font-size:16px;color:var(--blue);font-weight:500}
.call-sep{position:absolute;left:862px;top:18px;width:1px;height:46px;background:#ddd}
.socials{position:absolute;left:898px;top:22px;display:flex;gap:10px}
.social{width:40px;height:40px;border:2px solid #e4e4e4;border-radius:50%;display:flex;align-items:center;justify-content:center}
.social i{width:8px;height:8px;border-radius:50%;background:var(--blue)}
.nav{position:absolute;right:112px;top:78px;display:flex;gap:26px;font-size:16px;font-weight:500}
.nav a{color:var(--ink);text-decoration:none}
.nav a.active{color:var(--blue)}

/* hero */
.hero{position:absolute;left:0;top:112px;width:1200px;height:693px}
.hero-photo{position:absolute;inset:0;background:linear-gradient(180deg,#2f86d2 0%,#1f5fa8 35%,#2a3550 62%,#c98a2a 85%,#1c2a44 100%)}
.hero-box{position:absolute;left:258px;top:207px;width:684px;height:212px;background:rgba(60,60,70,.7);text-align:center;color:var(--white)}
.hero-box h1{font-family:"Montserrat",Arial,sans-serif;font-size:34px;font-weight:700;margin-top:24px}
.hero-box p{font-size:16px;font-weight:500;line-height:27px;margin-top:10px}
.hero-dots{position:absolute;left:568px;top:573px;display:flex;gap:6px}
.hero-dots i{width:10px;height:10px;border:1.5px solid var(--white)}
.hero-dots i.on{background:var(--blue)}
.hero-edge{position:absolute;left:0;top:520px}

/* about */
.about-art{position:absolute;left:109px;top:894px;width:414px;height:431px;background:linear-gradient(135deg,#3b3b3b,#a4512a 45%,#2aa3dc);clip-path:polygon(50% 0,100% 18%,100% 80%,50% 100%,0 80%,0 18%)}
.about h2{position:absolute;left:620px;top:933px;font-size:34px}
.about p{position:absolute;left:620px;width:469px;font-size:13.5px;line-height:24px;color:var(--text);text-align:justify}

/* services */
.services{position:absolute;left:0;top:1419px;width:1200px;height:661px;background:var(--grey-bg)}
.services h2{position:absolute;width:100%;top:40px;text-align:center;font-size:34px}
.services .intro{position:absolute;left:200px;width:800px;top:96px;text-align:center;font-size:15px;line-height:26px;color:var(--text)}
.service{position:absolute;top:193px;width:292px;height:330px;display:flex;flex-direction:column;align-items:center;justify-content:center;color:var(--white);text-align:center}
.service h3{font-size:17.5px;font-weight:700;text-transform:uppercase}
.service.active{background:var(--blue)}
.service.active p{font-size:13.5px;line-height:24px;padding:0 16px;margin-top:12px}
.service .icon{width:46px;height:46px;border:2px solid var(--white);border-radius:50%;margin-bottom:18px}
.service .more{margin-top:18px;border:2px solid var(--white);padding:10px 22px;font-weight:700;font-size:14px}
.arrow{position:absolute;top:579px;width:38px;height:38px;border-radius:50%;display:flex;align-items:center;justify-content:center}

/* why */
.why h2{position:absolute;width:100%;top:2166px;text-align:center;font-size:34px}
.why-col{position:absolute;top:2247px;width:310px;text-align:center}
.why-circle{width:106px;height:106px;margin:0 auto;border-radius:50%;border:2px solid #e6e6e6;box-shadow:0 3px 6px rgba(0,0,0,.08);display:flex;align-items:center;justify-content:center}
.why-circle i{width:48px;height:48px;border-radius:10px;background:var(--blue-pale);border:2px solid var(--blue)}
.why-col h3{font-size:19px;font-weight:700;margin-top:32px;text-transform:uppercase}
.why-col p{font-size:14.5px;line-height:24px;color:var(--text);margin-top:18px}

/* testimonials */
.testi{position:absolute;left:0;top:2586px;width:1200px;height:402px;background:linear-gradient(90deg,#1aa6e0,#20ace6 55%,#17a0db);color:var(--white)}
.testi h2{position:absolute;width:100%;top:38px;text-align:center;font-size:34px;color:var(--white)}
.testi-photo{position:absolute;left:111px;top:134px;width:184px;height:184px;border-radius:50%;border:4px solid var(--white);background:linear-gradient(160deg,#e9eef2,#8a9bab)}
.testi-badge{position:absolute;left:267px;top:197px;width:56px;height:56px;border-radius:50%;background:#333;color:var(--white);font-family:Georgia,serif;font-size:40px;display:flex;align-items:center;justify-content:center;line-height:1;padding-top:18px}
.testi-line{position:absolute;left:375px;top:130px;width:1px;height:190px;background:rgba(255,255,255,.6)}
.testi-quote{position:absolute;left:455px;top:125px;width:640px;font-size:14.5px;line-height:26px}
.testi-meta{position:absolute;left:455px;top:221px;display:flex;align-items:center;gap:26px;font-size:18px;font-weight:500;text-transform:uppercase}
.stars{color:#ffd200;font-size:22px;letter-spacing:2px}
.testi-btn{position:absolute;left:455px;top:275px;width:212px;height:45px;background:var(--white);color:var(--blue);font-size:14px;font-weight:500;display:flex;align-items:center;justify-content:center;text-transform:uppercase}
.testi-mark{position:absolute;left:960px;top:170px;font-family:Georgia,serif;font-size:260px;line-height:1;color:var(--white)}
.testi-dots{position:absolute;left:171px;top:349px;display:flex;gap:5px}
.testi-dots i{width:8px;height:8px;border-radius:50%;background:rgba(255,255,255,.5)}
.testi-dots i.on{background:var(--white)}

/* blog */
.blog h2{position:absolute;width:100%;top:3074px;text-align:center;font-size:34px}
.post{position:absolute;top:3152px;width:320px}
.post-img{position:relative;width:308px;height:248px}
.post-img::before{content:"";position:absolute;left:12px;top:12px;width:308px;height:248px;background:var(--blue-pale)}
.post-img i{position:absolute;inset:0}
.post h3{font-size:17px;font-weight:700;line-height:25px;margin-top:28px;width:300px}
.post a{display:block;margin-top:10px;font-size:15px;font-weight:500;color:var(--blue);text-decoration:none}

/* footer */
.footer-shape{position:absolute;left:0;top:3570px}
.footer-brand{position:absolute;left:109px;top:3758px;display:flex;align-items:center;gap:12px}
.footer-brand .brand-mark{width:64px;height:64px;background:var(--blue)}
.footer-brand span{font-family:"Montserrat",Arial,sans-serif;font-weight:700;font-size:24px;color:var(--white);line-height:1.05}
.footer-social{position:absolute;left:135px;top:3862px;display:flex;gap:11px}
.footer-social .social{border:none;background:var(--blue)}
.footer-social .social i{background:var(--white)}
.fcol{position:absolute;top:3748px;color:var(--white)}
.fcol h4{font-size:19px;font-weight:500}
.fcol h4::after{content:"";display:block;width:40px;height:2px;background:var(--blue);margin-top:10px}
.fcol ul{list-style:none;margin-top:18px}
.fcol li{font-size:14.5px;line-height:24px;display:flex;gap:20px;align-items:flex-start}
.fcol li b{flex:0 0 12px;height:12px;margin-top:6px;border:2px solid var(--blue);border-radius:50%}
.fcol.contact li{margin-bottom:6px}
.fcol.contact li svg{flex:0 0 14px;margin-top:5px}
.footer-rule{position:absolute;left:109px;top:3956px;width:980px;height:1px;background:#333}
.copy{position:absolute;width:100%;top:3981px;text-align:center;font-size:13px;color:var(--white)}
</style>
</head>
<body>

<header>
  <div class="brand"><div class="brand-mark"></div><div class="brand-name">Corlett &amp;<br>Associates</div></div>
  <div class="call">
    <svg width="42" height="42" viewBox="0 0 42 42"><circle cx="21" cy="21" r="19" fill="none" stroke="#16a3e0" stroke-width="2"/><path d="M14 12l5 1 1 5-3 2c1 3 3 5 6 6l2-3 5 1 1 5c-9 1-17-7-17-17z" fill="#16a3e0"/></svg>
    <div class="call-text"><small>Call Us:</small><span>(555) 014 2290</span></div>
  </div>
  <div class="call-sep"></div>
  <div class="socials" aria-label="Social links">
    <div class="social"><i></i></div><div class="social"><i></i></div><div class="social"><i></i></div><div class="social"><i></i></div>
  </div>
  <nav class="nav"><a class="active" href="#">Home</a><a href="#">About Us</a><a href="#">Our Services</a><a href="#">Why Choose Us</a><a href="#">Blog</a><a href="#">Contact Us</a></nav>
</header>

<section class="hero">
  <div class="hero-photo" role="img" aria-label="Harbour city skyline at dusk with lit buildings and opera house"></div>
  <div class="hero-box">
    <h1>CORLETT ASSOCIATES</h1>
    <p>Corlett Associates is specialised manufacturing engineering support organisation<br>that can provide fast, nimble, and flexible services.</p>
  </div>
  <div class="btn" style="left:528px;top:363px;width:144px;height:44px;font-size:14px">Get Started</div>
  <div class="hero-dots"><i></i><i class="on"></i><i></i><i></i></div>
  <svg class="hero-edge" width="1200" height="173" viewBox="0 0 1200 173">
    <path d="M0 40 Q300 140 600 150 Q900 140 1200 40 L1200 173 L0 173Z" fill="#16a3e0"/>
    <path d="M0 70 L600 173 L1200 70 L1200 173 L0 173Z" fill="#ffffff"/>
  </svg>
</section>

<section class="about">
  <div class="about-art" role="img" aria-label="Hexagonal collage of engineers and factory machinery"></div>
  <h2 class="heading">About Us</h2>
  <p style="top:993px">Corlett &amp; Associates is specialised manufacturing engineering support organisation that can provide fast, nimble, and flexible services. We have a proven track record in delivering tangible outcomes in process design and fit-out, project management, manufacturing process and maintenance design and execution.</p>
  <p style="top:1129px">Our specialist focus in food manufacturing across a range of sectors allows our team to deliver real benefits to performance and recognition of the clients investment.</p>
  <div class="btn" style="left:620px;top:1231px;width:133px;height:46px;font-size:14px">Learn More</div>
</section>

<section class="services">
  <h2 class="heading">Our Services</h2>
  <p class="intro">Sed ut perspiciatis unde omnis iste natus error sit voluptatem accusantium doloremque laudantium, totam rem aperiam, eaque ipsa quae ab illo inventore veritatis et</p>
  <div class="service" style="left:6px;background:linear-gradient(160deg,#6f8aa6,#3c5672)" role="img" aria-label="Engineers reviewing plans in an office"><h3>Project Management</h3></div>
  <div class="service" style="left:304px;background:linear-gradient(160deg,#c7d2dc,#7f95ab)" role="img" aria-label="Optical inspection camera equipment"><h3>Vision Inspection Systems</h3></div>
  <div class="service active" style="left:603px">
    <div class="icon"></div>
    <h3>Maintenance Execution</h3>
    <p>Sed ut perspiciatis unde omnis iste natu error sit voluptatem accusantium doloremque laudan.</p>
    <div class="more">READ MORE</div>
  </div>
  <div class="service" style="left:902px;background:linear-gradient(160deg,#9aa0a4,#3d4650)" role="img" aria-label="Engineers in hard hats reviewing a tablet on site"><h3>Acquisition Due Diligence</h3></div>
  <div class="arrow" style="left:556px;background:var(--white);border:1px solid #ddd"><svg width="14" height="14" viewBox="0 0 14 14"><path d="M8 2L3 7l5 5M3 7h10" stroke="#16a3e0" stroke-width="2.4" fill="none"/></svg></div>
  <div class="arrow" style="left:604px;background:var(--blue)"><svg width="14" height="14" viewBox="0 0 14 14"><path d="M6 2l5 5-5 5M11 7H1" stroke="#fff" stroke-width="2.4" fill="none"/></svg></div>
</section>

<section class="why">
  <h2 class="heading">Why Choose Us</h2>
  <div class="why-col" style="left:111px"><div class="why-circle"><i></i></div><h3>The Standard Lorem</h3><p>Lorem ipsum dolor sit amet, consectetur adi piscing elit, sed do eiusmod tempor inc ididunt ut labore et dolore.</p></div>
  <div class="why-col" style="left:447px"><div class="why-circle"><i></i></div><h3>The Standard Lorem</h3><p>Lorem ipsum dolor sit amet, consectetur adi piscing elit, sed do eiusmod tempor inc ididunt ut labore et dolore.</p></div>
  <div class="why-col" style="left:783px"><div class="why-circle"><i></i></div><h3>The Standard Lorem</h3><p>Lorem ipsum dolor sit amet, consectetur adi piscing elit, sed do eiusmod tempor inc ididunt ut labore et dolore.</p></div>
</section>

<section class="testi">
  <h2 class="heading">Testimonials</h2>
  <div class="testi-photo" role="img" aria-label="Portrait of a smiling client in a suit"></div>
  <div class="testi-badge">&ldquo;</div>
  <div class="testi-line"></div>
  <p class="testi-quote">Lorem ipsum dolor sit amet, consectetur adipiscing elit, sed do eiusmod tempor incididunt ut labore et dolore magna aliqua. Ut enim ad minim veniam, quis nostrud exercitation ullamco laboris nisi ut aliquip ex ea commodo consequat.</p>
  <div class="testi-meta"><span class="stars">★★★★★</span><span>Daniel Reyes</span></div>
  <div class="testi-btn">View All Testimonials</div>
  <div class="testi-mark">&rdquo;</div>
  <div class="testi-dots"><i></i><i class="on"></i><i></i><i></i><i></i></div>
</section>

<section class="blog">
  <h2 class="heading">Latest Blog</h2>
  <article class="post" style="left:109px"><div class="post-img"><i role="img" aria-label="Team meeting with engineers in hard hats" style="background:linear-gradient(150deg,#d9d3c6,#8d8679)"></i></div><h3>Lorem ipsum dolor sit amet, con sectetur adipiscing</h3><a href="#">Read More &nbsp;⊙</a></article>
  <article class="post" style="left:441px"><div class="post-img"><i role="img" aria-label="Two engineers checking a clipboard in a factory" style="background:linear-gradient(150deg,#7d8ea0,#2e4a6d)"></i></div><h3>Lorem ipsum dolor sit amet, con sectetur adipiscing</h3><a href="#">Read More &nbsp;⊙</a></article>
  <article class="post" style="left:771px"><div class="post-img"><i role="img" aria-label="Engineers reviewing drawings in a warehouse" style="background:linear-gradient(150deg,#8da1b8,#3c4f66)"></i></div><h3>Lorem ipsum dolor sit amet, con sectetur adipiscing</h3><a href="#">Read More &nbsp;⊙</a></article>
</section>

<footer>
  <svg class="footer-shape" width="1200" height="455" viewBox="0 0 1200 455">
    <path d="M0 128 L600 8 L1200 128 L1200 455 L0 455Z" fill="#16a3e0"/>
    <path d="M0 145 L600 32 L1200 145 L1200 455 L0 455Z" fill="#000000"/>
  </svg>
  <div class="footer-brand"><div class="brand-mark"></div><span>Valtrix<br>Engineering</span></div>
  <div class="footer-social" aria-label="Social links"><div class="social"><i></i></div><div class="social"><i></i></div><div class="social"><i></i></div><div class="social"><i></i></div></div>
  <div class="fcol" style="left:423px"><h4>Quick Links</h4><ul><li><b></b>Home</li><li><b></b>About Us</li><li><b></b>Our services</li><li><b></b>Why Choose Us</li><li><b></b>Blog</li></ul></div>
  <div class="fcol" style="left:629px"><h4>About</h4><ul><li><b></b>Site Map</li><li><b></b>Priacy Policy</li><li><b></b>Term &amp; Conditions</li></ul></div>
  <div class="fcol contact" style="left:859px"><h4>Contact Us</h4><ul>
    <li><svg width="14" height="14" viewBox="0 0 14 14"><path d="M7 1a4 4 0 014 4c0 3-4 8-4 8S3 8 3 5a4 4 0 014-4z" fill="#16a3e0"/><circle cx="7" cy="5" r="1.5" fill="#000"/></svg><span>27 Harbour Lane,<br>Australia</span></li>
    <li><svg width="14" height="14" viewBox="0 0 14 14"><path d="M2 2l3 0 1 3-2 1c1 2 2 3 4 4l1-2 3 1 0 3C6 12 2 8 2 2z" fill="#16a3e0"/></svg><span>(555) 014 2290</span></li>
    <li><svg width="14" height="14" viewBox="0 0 14 14"><rect x="1" y="3" width="12" height="9" fill="none" stroke="#16a3e0" stroke-width="1.5"/><path d="M1 3l6 5 6-5" fill="none" stroke="#16a3e0" stroke-width="1.5"/></svg><span>info@corlettassociates.example</span></li>
  </ul></div>
  <div class="footer-rule"></div>
  <p class="copy">Copyrights 2021 CORLETT ASSOCIATES. All rights reserved</p>
</footer>

</body>
</html>
```